House flipping business web site needed

pinecrestholdingsgroup.example.
I am a residential developer in Northern NJ and I am looking for a fresh new updated website. I have an intro video about my company being made now. I don't update it very often but I want an easy format that I can add update photos to on projects I have worked on or homes I renovate for sale.

Target Market(s)

investors into my projects so a portfolio , people looking to sell their homes to me.

Industry/Entity Type

Real Estate Development

Number of Pages Required

4 page

Font styles to use
Serif

Colors
33b8a4
39a9d7
cadf82

Requirements
Must have
• space for an intro video about my company
• a portfolio with pictures and information about each project
• Markets we serve- Morris County, NJ
• My logo- already created
• SEO
• Yes I would like this to function over all platforms. Phone, computer, all platforms.
• history and background page
• I am looking for a completed page that I can upload to the site that hosts my website
Nice to have
• I want something creative, easy to navigate. modern.

```html
<!DOCTYPE html>
<html lang="en">
<head>
<meta charset="utf-8">
<title>Pinecrest Holdings – Home</title>
<link rel="stylesheet" href="https://fonts.googleapis.com/css2?family=Raleway:wght@400;500;600&family=Arimo:wght@400;700&family=Courgette&family=PT+Serif&display=swap">
<style>
:root{
  --blue:#39a9d7;
  --blue-dark:#2f97c6;
  --page:#f4f4f3;
  --white:#ffffff;
  --text:#7a7a7a;
  --ink:#2f2f2f;
  --line:#dcdcdc;
}
*{box-sizing:border-box;margin:0;padding:0}
html,body{width:1200px;height:2830px;overflow:hidden}
body{position:relative;background:var(--page);font-family:"Arimo",Arial,sans-serif;color:var(--text)}
.abs{position:absolute}
.topbar{left:0;top:0;width:1200px;height:42px;background:var(--blue);color:var(--white);font-size:17px;display:flex;justify-content:flex-end;align-items:center;gap:34px;padding-right:80px;z-index:2}
.topbar span{display:flex;align-items:center;gap:10px}
.header{left:0;top:42px;width:1200px;height:98px;background:var(--white)}
.brand{left:85px;top:77px;display:flex;align-items:center;gap:10px;font-family:"Raleway",sans-serif;font-weight:600;font-size:22px;line-height:28px;color:var(--blue);letter-spacing:1px}
.brand i{width:18px;height:18px;border-radius:50%;background:var(--blue);display:block}
.nav{top:68px;left:536px;display:flex;align-items:center;font-family:"Raleway",sans-serif;font-size:16px;color:#555;text-transform:uppercase}
.nav a{color:inherit;text-decoration:none;margin-right:46px}
.nav .active{background:var(--blue);color:var(--white);width:92px;height:45px;display:flex;align-items:center;justify-content:center;margin-right:44px;font-weight:600}
.search{left:1098px;top:76px}
.hero{left:0;top:140px;width:1200px;height:536px;background:linear-gradient(180deg,#8cc5e4 0%,#b7d6e6 45%,#7f9a6a 70%,#4d92b6 100%)}
.hero-title{right:77px;top:305px;text-align:right;font-family:"Courgette",cursive;font-size:50px;line-height:61px;color:var(--white);text-shadow:0 2px 4px rgba(0,0,0,.35)}
.btn{background:var(--blue);color:var(--white);font-family:"Raleway",sans-serif;text-transform:uppercase;display:flex;align-items:center;justify-content:center}
.hero-btn{left:851px;top:459px;width:270px;height:60px;font-size:21px;box-shadow:0 3px 6px rgba(0,0,0,.3)}
.quote{left:0;top:676px;width:1200px;height:211px;background:var(--blue)}
.quote h2{position:absolute;width:1200px;top:45px;text-align:center;font-family:"Raleway",sans-serif;font-weight:400;font-size:40px;color:var(--white)}
.qfield{top:789px;height:51px;border:1px solid rgba(255,255,255,.85);color:var(--white);font-size:14px;padding:14px 10px}
.qsubmit{left:908px;top:789px;width:166px;height:51px;background:var(--white);color:var(--blue);font-family:"Raleway",sans-serif;font-size:21px;display:flex;align-items:center;justify-content:center}
h2.section{font-family:"Raleway",sans-serif;font-weight:400;color:var(--blue);font-size:40px;text-transform:uppercase}
.about-text{left:79px;top:1005px;width:680px;font-size:13px;line-height:26px}
.about-text p{margin-bottom:10px}
.about-btn{left:77px;top:1215px;width:176px;height:55px;font-size:20px}
.video{left:779px;top:953px;width:344px;height:317px;background:#000}
.video .frame{position:absolute;left:0;top:23px;width:344px;height:268px;background:linear-gradient(180deg,#a97a3b 0%,#c9b06a 28%,#3f6fa3 45%,#2c5b92 100%)}
.video svg{position:absolute;left:147px;top:135px}
.divider{left:79px;width:1044px;height:2px;background:var(--line)}
.center{width:1200px;text-align:center;left:0}
.pf-desc{left:170px;top:1455px;width:860px;text-align:center;font-size:13px;line-height:28px}
.card{width:250px;height:238px;background:var(--white);border:1px solid #e4e4e4}
.card .photo{height:156px;position:relative}
.card .price{position:absolute;right:0;bottom:0;background:var(--blue);color:var(--white);font-size:15px;padding:6px 10px}
.card h3{font-family:"Raleway",sans-serif;font-weight:600;font-size:16px;color:var(--ink);margin:13px 0 0 12px}
.specs{display:flex;align-items:center;gap:8px;margin:10px 0 0 12px;font-size:12px;color:#888}
.specs .dot{width:4px;height:4px;border-radius:50%;background:#bbb}
.p1{background:linear-gradient(180deg,#8fc2e3,#c9c2b2 55%,#5f8f4c)}
.p2{background:linear-gradient(180deg,#9fb8cc,#b59a86 55%,#7c6a5c)}
.p3{background:linear-gradient(180deg,#3b3633,#1f1c1a 60%,#5f6b4f)}
.p4{background:linear-gradient(180deg,#a9c5d8,#7f8a5e 50%,#a3685a)}
.p5{background:linear-gradient(180deg,#8bbbe0,#a3a288 50%,#4f8d3d)}
.p6{background:linear-gradient(180deg,#7bb3df,#5c5240 50%,#6e8550)}
.contact-left{left:79px;top:2220px;width:500px}
.contact-left h3{font-family:"Raleway",sans-serif;font-weight:400;font-size:32px;color:var(--blue);text-transform:uppercase}
.contact-left p{font-size:13px;line-height:23px;margin-top:8px}
.touch{left:79px;top:2400px;font-family:"Raleway",sans-serif;font-size:25px;color:var(--blue);text-transform:uppercase}
.ci{left:77px;display:flex;gap:20px;font-size:13px;line-height:23px;color:#555}
.field{left:623px;width:500px;height:51px;background:var(--white);border:1px solid #d6d6d6;font-size:13px;color:#999;padding:17px 20px}
.fsubmit{left:623px;top:2513px;width:500px;height:51px;font-family:"PT Serif",serif;font-size:21px;text-transform:uppercase}
.footer{left:0;top:2627px;width:1200px;height:203px;background:var(--blue);color:var(--white)}
.fnav{left:77px;top:2643px;display:flex;align-items:center;font-size:15px;color:var(--white)}
.fnav span{margin-right:56px}
.fnav .active{border:1px solid var(--white);width:83px;height:44px;display:flex;align-items:center;justify-content:center;margin-right:30px}
.social{top:2646px;width:36px;height:36px;border-radius:50%;border:2px solid var(--white)}
.fline{left:77px;top:2706px;width:1046px;height:1px;background:rgba(255,255,255,.7)}
.fhead{left:79px;top:2722px;font-family:"Raleway",sans-serif;font-size:17px;color:var(--white);letter-spacing:1px}
.fitem{top:2752px;display:flex;align-items:center;gap:22px;font-size:14px;line-height:22px;color:var(--white)}
.fitem.mail{gap:14px;font-size:12px;line-height:18px}
.fcircle{width:52px;height:52px;border-radius:50%;border:2px solid var(--white);display:flex;align-items:center;justify-content:center;flex:none}
.fcircle.solid{background:var(--white)}
.copy{left:884px;top:2766px;font-size:14px;line-height:24px;color:var(--white)}
.copy b{font-weight:700}
</style>
</head>
<body>

<div class="abs topbar">
  <span><svg width="18" height="18" viewBox="0 0 24 24" fill="none" stroke="#fff" stroke-width="2"><path d="M5 3h4l2 5-3 2a11 11 0 0 0 6 6l2-3 5 2v4a2 2 0 0 1-2 2A17 17 0 0 1 3 5a2 2 0 0 1 2-2z"/></svg>123 456 7890</span>
  <span><svg width="20" height="16" viewBox="0 0 24 18" fill="none" stroke="#fff" stroke-width="2"><rect x="1" y="1" width="22" height="16"/><path d="M1 1l11 9 11-9"/></svg>info@pinecrestholdingsgroup.example</span>
</div>

<header class="abs header"></header>
<div class="abs brand"><i></i>PINECREST HOLDINGS</div>
<nav class="abs nav">
  <a class="active" href="#">Home</a><a href="#">About Us</a><a href="#">Portfolio</a><a href="#">Contact Us</a>
</nav>
<svg class="abs search" width="26" height="26" viewBox="0 0 24 24" fill="none" stroke="#39a9d7" stroke-width="3"><circle cx="10" cy="10" r="7"/><path d="M15 15l7 7"/></svg>

<div class="abs hero" role="img" aria-label="Large white shingle-style house with a swimming pool and lawn under a blue sky"></div>
<h1 class="abs hero-title">We will help you get out of<br>your unwanted home</h1>
<div class="abs btn hero-btn">Contact us know</div>

<section class="abs quote"><h2>GET A QUOTE</h2></section>
<div class="abs qfield" style="left:126px;width:250px">Name*</div>
<div class="abs qfield" style="left:387px;width:249px">Email*</div>
<div class="abs qfield" style="left:647px;width:249px">Message*</div>
<div class="abs qsubmit">SUBMIT</div>

<h2 class="abs section" style="left:79px;top:945px">About Pinecrest</h2>
<div class="abs about-text">
  <p>Pinecrest Holdings is a family run business with 3rd generation builders and renovators in the Morris County area. As the President and owner of Pinecrest Holdings I am dedicated to working hard to create opportunities for investment through real estate.</p>
  <p>At Pinecrest Holdings we have a valuable support system and a team of investors, realtors, attorneys, contractors and property managers providing a combined package offering years of experience in the local market. Dana Whitfield: President and owner<br>Licensed Real Estate Referral Agent</p>
</div>
<div class="abs btn about-btn">Know more</div>
<div class="abs video">
  <div class="frame" role="img" aria-label="Intro video still: the owner seated by a lake with autumn trees behind"></div>
  <svg width="50" height="50" viewBox="0 0 50 50"><circle cx="25" cy="25" r="22" fill="none" stroke="#39a9d7" stroke-width="3"/><path d="M19 14l17 11-17 11z" fill="#39a9d7"/></svg>
</div>

<div class="abs divider" style="top:1337px"></div>

<h2 class="abs section center" style="top:1395px">Our Portfolio</h2>
<p class="abs pf-desc">Many upgrades to this home, Added a new full bath, family room, office, kitchenette and kids play room in walk out basement with 2 triple french doors. New 1/2 bath was added off of the dining room with large.</p>

<div class="abs card" style="left:77px;top:1527px"><div class="photo p1" role="img" aria-label="Shingle-style house with pool"><span class="price">$300000</span></div><h3>33 Pinecrest Holdings</h3><div class="specs"><svg width="14" height="14" viewBox="0 0 14 14" stroke="#888" fill="none" stroke-width="1.5"><path d="M2 12L12 2M8 2h4v4M2 8v4h4"/></svg>2600 sq<i class="dot"></i><svg width="18" height="12" viewBox="0 0 18 12" stroke="#888" fill="none" stroke-width="1.5"><path d="M1 1v10M1 8h16v3M4 5h12v3"/></svg>4<i class="dot"></i><svg width="16" height="14" viewBox="0 0 16 14" stroke="#888" fill="none" stroke-width="1.5"><path d="M1 7h14v3a3 3 0 0 1-3 3H4a3 3 0 0 1-3-3zM3 7V2h3"/></svg>2</div></div>
<div class="abs card" style="left:343px;top:1527px"><div class="photo p2" role="img" aria-label="Two-storey house with turret windows"><span class="price">$380/pw</span></div><h3>33 Pinecrest Holdings</h3><div class="specs"><svg width="14" height="14" viewBox="0 0 14 14" stroke="#888" fill="none" stroke-width="1.5"><path d="M2 12L12 2M8 2h4v4M2 8v4h4"/></svg>2600 sq<i class="dot"></i><svg width="18" height="12" viewBox="0 0 18 12" stroke="#888" fill="none" stroke-width="1.5"><path d="M1 1v10M1 8h16v3M4 5h12v3"/></svg>4<i class="dot"></i><svg width="16" height="14" viewBox="0 0 16 14" stroke="#888" fill="none" stroke-width="1.5"><path d="M1 7h14v3a3 3 0 0 1-3 3H4a3 3 0 0 1-3-3zM3 7V2h3"/></svg>2</div></div>
<div class="abs card" style="left:608px;top:1527px"><div class="photo p3" role="img" aria-label="Renovated entry doorway opening onto a yard"><span class="price">$400/pw</span></div><h3>33 Pinecrest Holdings</h3><div class="specs"><svg width="14" height="14" viewBox="0 0 14 14" stroke="#888" fill="none" stroke-width="1.5"><path d="M2 12L12 2M8 2h4v4M2 8v4h4"/></svg>2600 sq<i class="dot"></i><svg width="18" height="12" viewBox="0 0 18 12" stroke="#888" fill="none" stroke-width="1.5"><path d="M1 1v10M1 8h16v3M4 5h12v3"/></svg>4<i class="dot"></i><svg width="16" height="14" viewBox="0 0 16 14" stroke="#888" fill="none" stroke-width="1.5"><path d="M1 7h14v3a3 3 0 0 1-3 3H4a3 3 0 0 1-3-3zM3 7V2h3"/></svg>2</div></div>
<div class="abs card" style="left:872px;top:1527px"><div class="photo p4" role="img" aria-label="Single-storey house with porch and trees"><span class="price">$480/pw</span></div><h3>33 Pinecrest Holdings</h3><div class="specs"><svg width="14" height="14" viewBox="0 0 14 14" stroke="#888" fill="none" stroke-width="1.5"><path d="M2 12L12 2M8 2h4v4M2 8v4h4"/></svg>2600 sq<i class="dot"></i><svg width="18" height="12" viewBox="0 0 18 12" stroke="#888" fill="none" stroke-width="1.5"><path d="M1 1v10M1 8h16v3M4 5h12v3"/></svg>4<i class="dot"></i><svg width="16" height="14" viewBox="0 0 16 14" stroke="#888" fill="none" stroke-width="1.5"><path d="M1 7h14v3a3 3 0 0 1-3 3H4a3 3 0 0 1-3-3zM3 7V2h3"/></svg>2</div></div>

<div class="abs card" style="left:77px;top:1779px"><div class="photo p5" role="img" aria-label="Ranch house behind a green lawn"><span class="price">$300000</span></div><h3>33 Pinecrest Holdings</h3><div class="specs"><svg width="14" height="14" viewBox="0 0 14 14" stroke="#888" fill="none" stroke-width="1.5"><path d="M2 12L12 2M8 2h4v4M2 8v4h4"/></svg>2600 sq<i class="dot"></i><svg width="18" height="12" viewBox="0 0 18 12" stroke="#888" fill="none" stroke-width="1.5"><path d="M1 1v10M1 8h16v3M4 5h12v3"/></svg>4<i class="dot"></i><svg width="16" height="14" viewBox="0 0 16 14" stroke="#888" fill="none" stroke-width="1.5"><path d="M1 7h14v3a3 3 0 0 1-3 3H4a3 3 0 0 1-3-3zM3 7V2h3"/></svg>2</div></div>
<div class="abs card" style="left:343px;top:1779px"><div class="photo p6" role="img" aria-label="Dark brick house with unfinished yard"><span class="price">$380/pw</span></div><h3>33 Pinecrest Holdings</h3><div class="specs"><svg width="14" height="14" viewBox="0 0 14 14" stroke="#888" fill="none" stroke-width="1.5"><path d="M2 12L12 2M8 2h4v4M2 8v4h4"/></svg>2600 sq<i class="dot"></i><svg width="18" height="12" viewBox="0 0 18 12" stroke="#888" fill="none" stroke-width="1.5"><path d="M1 1v10M1 8h16v3M4 5h12v3"/></svg>4<i class="dot"></i><svg width="16" height="14" viewBox="0 0 16 14" stroke="#888" fill="none" stroke-width="1.5"><path d="M1 7h14v3a3 3 0 0 1-3 3H4a3 3 0 0 1-3-3zM3 7V2h3"/></svg>2</div></div>
<div class="abs card" style="left:608px;top:1779px"><div class="photo p3" role="img" aria-label="Renovated entry doorway opening onto a yard"><span class="price">$400/pw</span></div><h3>33 Pinecrest Holdings</h3><div class="specs"><svg width="14" height="14" viewBox="0 0 14 14" stroke="#888" fill="none" stroke-width="1.5"><path d="M2 12L12 2M8 2h4v4M2 8v4h4"/></svg>2600 sq<i class="dot"></i><svg width="18" height="12" viewBox="0 0 18 12" stroke="#888" fill="none" stroke-width="1.5"><path d="M1 1v10M1 8h16v3M4 5h12v3"/></svg>4<i class="dot"></i><svg width="16" height="14" viewBox="0 0 16 14" stroke="#888" fill="none" stroke-width="1.5"><path d="M1 7h14v3a3 3 0 0 1-3 3H4a3 3 0 0 1-3-3zM3 7V2h3"/></svg>2</div></div>
<div class="abs card" style="left:872px;top:1779px"><div class="photo p4" role="img" aria-label="Single-storey house with porch and trees"><span class="price">$480/pw</span></div><h3>33 Pinecrest Holdings</h3><div class="specs"><svg width="14" height="14" viewBox="0 0 14 14" stroke="#888" fill="none" stroke-width="1.5"><path d="M2 12L12 2M8 2h4v4M2 8v4h4"/></svg>2600 sq<i class="dot"></i><svg width="18" height="12" viewBox="0 0 18 12" stroke="#888" fill="none" stroke-width="1.5"><path d="M1 1v10M1 8h16v3M4 5h12v3"/></svg>4<i class="dot"></i><svg width="16" height="14" viewBox="0 0 16 14" stroke="#888" fill="none" stroke-width="1.5"><path d="M1 7h14v3a3 3 0 0 1-3 3H4a3 3 0 0 1-3-3zM3 7V2h3"/></svg>2</div></div>

<div class="abs divider" style="top:2084px"></div>

<h2 class="abs section center" style="top:2140px">Contact Us</h2>
<div class="abs contact-left">
  <h3>Pinecrest</h3>
  <p>We only buy and renovate homes in our neighborhoods right here in the Morris County, NJ area.<br>Is a house in your neighborhood an eyesore? Is it vacant, boarded up and a hazard to the neighborhood? Please contact us and we can help transform that property into a beautiful home.</p>
</div>
<div class="abs touch">Get in touch</div>
<div class="abs ci" style="top:2448px"><svg width="22" height="18" viewBox="0 0 22 18" fill="none" stroke="#39a9d7" stroke-width="1.6"><path d="M1 3l6-2 8 2 6-2v14l-6 2-8-2-6 2zM7 1v14M15 3v14"/></svg><span>101- Lorem ipsum is simple dummy text<br>of printing and type setting.</span></div>
<div class="abs ci" style="top:2508px"><svg width="22" height="22" viewBox="0 0 24 24" fill="none" stroke="#39a9d7" stroke-width="1.8"><path d="M5 3h4l2 5-3 2a11 11 0 0 0 6 6l2-3 5 2v4a2 2 0 0 1-2 2A17 17 0 0 1 3 5a2 2 0 0 1 2-2z"/></svg><span>123 456 7890</span></div>
<div class="abs ci" style="top:2546px"><svg width="22" height="17" viewBox="0 0 24 18" fill="none" stroke="#39a9d7" stroke-width="1.8"><rect x="1" y="1" width="22" height="16"/><path d="M1 1l11 9 11-9"/></svg><span>info@pinecrestholdingsgroup.example</span></div>

<div class="abs field" style="top:2219px">Name</div>
<div class="abs field" style="top:2280px">E-Mail Address</div>
<div class="abs field" style="top:2340px">Phone</div>
<div class="abs field" style="top:2400px;height:104px">Message</div>
<div class="abs btn fsubmit">Submit</div>

<footer class="abs footer"></footer>
<div class="abs fnav"><span class="active">Home</span><span>About Us</span><span>Portfolio</span><span>Contact Us</span></div>
<div class="abs social" style="left:997px"></div>
<div class="abs social" style="left:1042px"></div>
<div class="abs social" style="left:1087px"></div>
<div class="abs fline"></div>
<div class="abs fhead">CONTACT US</div>
<div class="abs fitem" style="left:77px"><div class="fcircle solid"><svg width="20" height="26" viewBox="0 0 20 26"><path d="M10 1a9 9 0 0 1 9 9c0 7-9 15-9 15S1 17 1 10a9 9 0 0 1 9-9z" fill="#39a9d7"/><circle cx="10" cy="10" r="3.5" fill="#fff"/></svg></div><span>101- Lorem ipsum is dummy<br>text of print and type.</span></div>
<div class="abs fitem" style="left:352px"><div class="fcircle"><svg width="22" height="22" viewBox="0 0 24 24" fill="#fff"><path d="M5 3h4l2 5-3 2a11 11 0 0 0 6 6l2-3 5 2v4a2 2 0 0 1-2 2A17 17 0 0 1 3 5a2 2 0 0 1 2-2z"/></svg></div><span>123 456 7890</span></div>
<div class="abs fitem mail" style="left:606px"><div class="fcircle"><svg width="22" height="17" viewBox="0 0 24 18" fill="none" stroke="#fff" stroke-width="2"><rect x="1" y="1" width="22" height="16"/><path d="M1 1l11 9 11-9"/></svg></div><span>office@<br>pinecrestholdingsgroup.example</span></div>
<div class="abs copy"><b>PINECREST HOLDINGS</b><br>2016, All rights reserved.</div>

</body>
</html>
```